Business Card design for law firm = Brightvale Australia

We are seeking a new design for our business cards.
We are keeping our logo, which is attached.
We need space for
Name
Title
Address is , which is
Level 7
214 Marlowe Street
Sydney NSW 2047
Phone :
Mobile :
Fax :
Email :
DX :
website www.brightvale-example.com.au

Industry/Entity Type

Law Firm / Banking and Finance

Contact Information for Business Card

We are seeking a new design for our business cards. We are keeping our logo. We need space for Name Title Address is Level 7 214 Marlowe Street Sydney NSW 2047 Phone Mobile Fax Email DX website www.brightvale-example.com.au

Colors
0054AA
0677BA
7BADD7
CADEEF
E8F1F8

Requirements
Must have
• see our website for general feel www.brightvale-example.com.au

```html
<!DOCTYPE html>
<html lang="en">
<head>
<meta charset="utf-8">
<title>Brightvale Australia – Business Card</title>
<link rel="stylesheet" href="https://fonts.googleapis.com/css2?family=Crimson+Text:wght@400&family=Open+Sans:wght@300&display=swap">
<style>
  :root {
    --backdrop: #8f8f8f;
    --paper: #ffffff;
    --brand-blue: #0957a3;
    --brand-teal: #0596bb;
    --ink: #4a4a4a;
    --shadow: rgba(0,0,0,0.35);
  }
  * { box-sizing: border-box; margin: 0; padding: 0; }
  html, body { width: 1200px; height: 1200px; overflow: hidden; }
  body { background: var(--backdrop); position: relative; font-family: "Crimson Text", Georgia, serif; }

  .card {
    position: absolute; left: 281px; width: 639px; height: 367px;
    box-shadow: 2px 2px 2px var(--shadow);
  }
  .card--front { top: 195px; background: var(--paper); }
  .card--back { top: 639px; background: var(--brand-blue); }

  .front-brand { position: absolute; left: 22px; top: 30px; font-size: 20px; color: var(--brand-blue); }

  .address {
    position: absolute; right: calc(639px - 288px); top: 144px;
    text-align: right; font-size: 17px; line-height: 22.3px; color: var(--ink); font-style: normal;
  }
  .address__company { color: var(--brand-blue); }

  .divider { position: absolute; left: 310px; top: 150px; width: 1px; height: 87px; background: var(--brand-blue); }

  .contacts { position: absolute; left: 332px; top: 144px; list-style: none; font-size: 17px; line-height: 22.3px; color: var(--ink); letter-spacing: 0.3px; }
  .contacts li { display: flex; align-items: center; gap: 8px; }
  .contacts svg { width: 12px; height: 12px; fill: var(--brand-teal); flex: none; }

  .website {
    position: absolute; left: 0; right: 0; top: 303px; text-align: center;
    font-size: 15px; letter-spacing: 6px; color: var(--brand-blue); text-transform: uppercase;
  }

  .back-brand__name { position: absolute; left: 182px; top: 180px; font-size: 60px; line-height: 1; color: #ffffff; }
  .back-brand__tagline {
    position: absolute; left: 184px; top: 255px; font-family: "Open Sans", Arial, sans-serif;
    font-weight: 300; font-size: 19.5px; letter-spacing: 1.6px; color: var(--brand-teal);
  }
</style>
</head>
<body>
  <section class="card card--front">
    <div class="front-brand">Brightvale</div>

    <address class="address">
      <div class="address__company">Brightvale Australia Pty Ltd</div>
      <div>Level 7, 214 Marlowe Street</div>
      <div>Sydney NSW 2047</div>
      <div>DX 321 Sydney</div>
    </address>

    <div class="divider"></div>

    <ul class="contacts">
      <li><svg viewBox="0 0 12 12" aria-hidden="true"><path d="M2.5 0.8l2 2.2-1 1.3c.6 1.5 1.7 2.6 3.2 3.2l1.3-1 2.2 2-1.2 2c-4.5-.3-8-3.8-8.3-8.3z"/></svg>02 9000 1357</li>
      <li><svg viewBox="0 0 12 12" aria-hidden="true"><path d="M3 0h6a1 1 0 0 1 1 1v10a1 1 0 0 1-1 1H3a1 1 0 0 1-1-1V1a1 1 0 0 1 1-1zm.5 1.5v7.5h5V1.5zM6 9.8a.7.7 0 1 0 0 1.4.7.7 0 0 0 0-1.4z"/></svg>02 9000 2468</li>
      <li><svg viewBox="0 0 12 12" aria-hidden="true"><path d="M3 1h6v3H3zM1 4.5h10v5H9V8H3v1.5H1zM3.5 8.5h5V11h-5z"/></svg>02 9000 2468</li>
      <li><svg viewBox="0 0 12 12" aria-hidden="true"><path d="M1 3h10v6.5H1zM1.6 3.4L6 6.8l4.4-3.4v1L6 7.8 1.6 4.4z"/></svg>enquiries@brightvale-example.com.au</li>
    </ul>

    <div class="website">www.brightvale-example.com.au</div>
  </section>

  <section class="card card--back">
    <div class="back-brand__name">Brightvale</div>
    <div class="back-brand__tagline">practical legal solutions</div>
  </section>
</body>
</html>
```